Change of trading name, rebrand

existing website to be updated with new theme and logo. existing website is
www.harlowbrentmere.com.au
Industry/Entity Type
Construction
Coding
Coded - Design and coding required
Number of Pages Required
5+ page
Requirements
Must have
- be mobile phone friendly

```html
<!DOCTYPE html>
<html lang="en">
<head>
<meta charset="utf-8">
<title>HBR Plant Hire</title>
<link href="https://fonts.googleapis.com/css2?family=Poppins:wght@400;500;600;700;800&display=swap" rel="stylesheet">
<style>
:root{
  --purple:#2b1466;
  --purple-deep:#1c0c47;
  --purple-mid:#3d2285;
  --ink:#1a1a1a;
  --muted:#555;
  --grey-bg:#f1f1f3;
  --white:#fff;
  --black:#0b0b0b;
  --sky:#9fb8cf;
  --sand:#c9a46a;
}
*{box-sizing:border-box;margin:0;padding:0}
html,body{width:1200px;height:3800px;overflow:hidden}
body{font-family:'Poppins',sans-serif;color:var(--ink);background:var(--white);position:relative}
.abs{position:absolute}
/* header */
.topbar{top:0;left:0;width:1200px;height:140px;background:var(--white)}
.brand{left:40px;top:10px;width:190px;height:150px;display:flex;flex-direction:column;align-items:center;justify-content:center;z-index:3}
.brand-mark{width:70px;height:70px;border-radius:50%;background:var(--purple);margin-bottom:8px}
.brand-name{font-weight:800;font-size:30px;color:var(--purple);line-height:1}
.contact-strip{right:80px;top:22px;display:flex;gap:36px;font-size:15px;font-weight:500}
.contact-strip span{display:flex;align-items:center;gap:10px}
.ic{width:30px;height:30px;border-radius:50%;background:var(--purple);display:inline-flex;align-items:center;justify-content:center}
.nav{left:300px;top:88px;width:820px;height:46px;background:var(--purple);border-radius:6px;display:flex;align-items:center;justify-content:space-around;padding:0 20px;color:var(--white);font-size:15px;font-weight:500}
.nav .active{background:var(--white);color:var(--purple);padding:6px 14px;border-radius:4px}
/* hero */
.hero{top:140px;left:0;width:1200px;height:520px;background:linear-gradient(90deg,#2a1a5c 0%,#4a4e86 40%,#8fa3bf 70%,#c9b48a 100%)}
.hero-title{left:100px;top:236px;font-size:44px;font-weight:800;color:var(--white)}
.hero-copy{left:100px;top:300px;width:360px;font-size:14px;line-height:1.5;color:#e7e3f4}
.btn{display:inline-block;background:var(--purple);color:var(--white);border-radius:22px;padding:9px 26px;font-size:14px;font-weight:500}
.btn-outline{background:var(--white);color:var(--purple);border:2px solid var(--purple)}
.hero .btn{position:absolute;left:100px;top:328px}
.down{left:572px;top:632px;width:56px;height:56px;border-radius:50%;background:var(--white);border:3px solid var(--purple);display:flex;align-items:center;justify-content:center;z-index:2}
/* about */
.about-photo{left:80px;top:740px;width:380px;height:370px;border-radius:60px 20px 20px 20px;background:linear-gradient(160deg,#a7c0d8,#6f7f93 60%,#4b5a6a)}
.about-text{left:510px;top:740px;width:610px}
.about-text h2{font-size:36px;font-weight:700;line-height:1.15}
.about-text h3{font-size:30px;font-weight:500;line-height:1.25;margin-top:8px}
.about-text p{font-size:14px;line-height:1.6;color:var(--muted);margin-top:18px}
.about-text .btn{margin-top:22px}
.stats{left:100px;top:1188px;width:1000px;display:flex;gap:16px}
.stat{flex:1;height:64px;border:1px solid #ddd;border-radius:8px;display:flex;align-items:center;gap:10px;padding:0 12px;font-size:11px;line-height:1.2;color:var(--muted)}
.stat b{font-size:28px;color:var(--ink);font-weight:700}
.stat i{width:32px;height:32px;border:2px solid var(--purple);border-radius:6px;flex:none}
.machines{left:0;top:1290px;width:1200px;height:470px;background:linear-gradient(180deg,#ffffff 0%,#d9d6e4 40%,#2b1466 100%)}
/* services */
.services{left:0;top:1780px;width:1200px;height:520px;background:var(--grey-bg)}
.sec-title{width:1200px;text-align:center;font-size:36px;font-weight:700}
.sec-sub{width:1200px;text-align:center;font-size:14px;color:var(--muted);line-height:1.5}
.svc-list{left:140px;top:1970px;list-style:none;font-size:18px;font-weight:500}
.svc-list li{height:37px;display:flex;align-items:center;gap:14px}
.svc-list li::before{content:"";width:12px;height:12px;border-radius:50%;border:4px solid var(--purple);background:var(--white)}
.svc-list .on{color:var(--purple);font-weight:700}
.svc-card{left:440px;top:1970px;width:660px;height:280px;background:var(--white);border-radius:10px;padding:14px}
.svc-photo{position:absolute;left:14px;top:14px;width:300px;height:252px;border-radius:6px;background:linear-gradient(160deg,#a9c3d9,#c46a2a 60%,#8a6a4a)}
.svc-body{position:absolute;left:340px;top:28px;width:290px}
.svc-body h4{font-size:20px;font-weight:700}
.svc-body p{font-size:12px;line-height:1.55;color:var(--muted);margin:10px 0 18px}
/* partners */
.partners{left:40px;top:2440px;width:1120px;height:80px;display:flex;align-items:center;justify-content:space-between}
.arrow{font-size:40px;color:var(--ink);font-weight:300}
.badge{width:160px;height:56px;border-radius:8px;background:#e3e1ea}
/* contact */
.contact{left:0;top:2620px;width:1200px;height:600px;background:linear-gradient(180deg,var(--purple-mid),var(--purple-deep))}
.contact .sec-title,.contact .sec-sub{color:var(--white)}
.form-card{left:80px;top:2770px;width:1040px;height:410px;background:var(--white);border-radius:12px}
.field{position:absolute;left:22px;width:570px;height:50px;border:1px solid #ccc;border-radius:6px;font-size:14px;color:#555;padding:12px 16px}
.map{position:absolute;left:620px;top:16px;width:400px;height:270px;border-radius:8px;background:linear-gradient(135deg,#eef0ea,#d8dfd2)}
.form-card .btn{position:absolute;left:22px;top:355px}
/* footer */
.footer{left:0;top:3220px;width:1200px;height:580px;background:var(--black);color:var(--white)}
.f-brand{left:80px;top:3340px;display:flex;align-items:center;gap:16px}
.f-brand .brand-mark{background:var(--white);margin:0;width:80px;height:80px}
.f-brand .brand-name{color:var(--white);font-size:44px}
.socials{left:100px;top:3630px;display:flex;gap:12px}
.socials i{width:40px;height:40px;border-radius:50%;border:2px solid var(--white)}
.copy{left:80px;top:3700px;font-size:13px}
.f-col{top:3260px}
.f-col h5{font-size:17px;font-weight:700;margin-bottom:16px}
.f-col li{list-style:none;font-size:14px;line-height:30px;display:flex;align-items:center;gap:10px}
.f-col li::before{content:"";width:6px;height:6px;border-radius:50%;background:var(--white)}
.f-links{left:500px}
.f-do{left:800px}
</style>
</head>
<body>
<header class="abs topbar"></header>
<div class="abs brand"><div class="brand-mark"></div><div class="brand-name">HBR</div></div>
<div class="abs contact-strip">
  <span><i class="ic"><svg width="16" height="12" viewBox="0 0 16 12"><rect x="1" y="1" width="14" height="10" fill="none" stroke="#fff" stroke-width="1.5"/><path d="M1 1l7 6 7-6" fill="none" stroke="#fff" stroke-width="1.5"/></svg></i>info@harlowbrentmere.com</span>
  <span><i class="ic"><svg width="14" height="14" viewBox="0 0 24 24"><path d="M6 2l4 5-2 3c1 3 3 5 6 6l3-2 5 4-3 4C10 22 2 14 2 5z" fill="#fff"/></svg></i>1300 555 014</span>
</div>
<nav class="abs nav"><span class="active">Home</span><span>About us</span><span>Plant Hire</span><span>Major Project Snapshot</span><span>Policies</span><span>Jobs</span><span>Contact us</span></nav>

<section class="abs hero" role="img" aria-label="Yellow excavator lifting its bucket against a blue sky">
  <h1 class="abs hero-title" style="top:96px;left:100px">HBR HEAVY<br>EQUIPMENT HIRE</h1>
  <p class="abs hero-copy" style="top:220px">Harlow Brentmere Heavy Equipment Hire specialise in the hire of heavy earthmoving, mining and construction machines with specialised attachments and testing.</p>
  <span class="btn">Join Now</span>
</section>
<div class="abs down"><svg width="22" height="14" viewBox="0 0 22 14"><path d="M2 2l9 9 9-9" fill="none" stroke="#2b1466" stroke-width="3"/></svg></div>

<div class="abs about-photo" role="img" aria-label="Piling crane working beside a river on a construction site"></div>
<div class="abs about-text">
  <h2>HBR Heavy Equipment Hire</h2>
  <h3>Committed to superior quality plant hire services.</h3>
  <p>Harlow Brentmere Heavy Equipment Hire specialise in the hire of heavy earthmoving, mining and construction machines with specialised attachments and testing. Our range of machines and attachments is second to none, and we have one of the largest hire fleets available in South East Queensland. If a plant item is required, then Harlow Brentmere Resources, or HBR as the locals call us, should be the first call you make. With us, you receive skilled operators and quality machines across all makes and models to guarantee you maximum up-time.</p>
  <span class="btn btn-outline">Read More</span>
</div>
<div class="abs stats">
  <div class="stat"><i></i><b>20+</b>Years of<br>experience</div>
  <div class="stat"><i></i><b>100+</b>Machines in<br>fleet</div>
  <div class="stat"><i></i>One of QLD's<br>largest suppliers</div>
  <div class="stat"><i></i>Onsite<br>servicing</div>
  <div class="stat"><i></i>Custom machine<br>attachments</div>
</div>
<div class="abs machines" role="img" aria-label="Silhouettes of excavators, loaders, rollers and tipper trucks across a work site"></div>

<section class="abs services"></section>
<h2 class="abs sec-title" style="top:1810px">Our Services</h2>
<p class="abs sec-sub" style="top:1862px">We employ a group of highly skilled and capable managers who have worked throughout construction<br>sites in Queensland, NSW and other parts of Australia to</p>
<ul class="abs svc-list">
  <li class="on">Excavators</li><li>Dozers</li><li>Dump Trucks</li><li>Graders</li><li>Loaders</li><li>Bobcats</li><li>Water Carts</li><li>Backhoes</li><li>Compactors</li>
</ul>
<div class="abs svc-card">
  <div class="svc-photo" role="img" aria-label="Orange excavator digging on a job site"></div>
  <div class="svc-body">
    <h4>EXCAVATOR HIRE</h4>
    <p>With one of the largest fleets of excavators for hire in South East Queensland, HBR Heavy Equipment are proud of our wide range of diggers. All our excavators and diggers for hire are sourced from reputable makers and are serviced regularly. From small, nimble units to heavy duty machines, we can match the right excavator to your job and budget, with attachments and operators available on request.</p>
    <span class="btn btn-outline">Read More</span>
  </div>
</div>

<div class="abs partners">
  <span class="arrow">&#8249;</span>
  <div class="badge"></div><div class="badge"></div><div class="badge"></div><div class="badge"></div><div class="badge"></div>
  <span class="arrow">&#8250;</span>
</div>

<section class="abs contact"></section>
<h2 class="abs sec-title" style="top:2650px;color:#fff">Contact Us Today For A Free Quote</h2>
<p class="abs sec-sub" style="top:2700px;color:#fff">We employ a group of highly skilled and capable managers who have worked throughout construction<br>sites in Queensland, NSW and other parts of Australia to</p>
<div class="abs form-card">
  <div class="field" style="top:16px">Name *</div>
  <div class="field" style="top:80px">Email *</div>
  <div class="field" style="top:144px">Phone *</div>
  <div class="field" style="top:208px;height:130px">Enquiry *</div>
  <div class="map" role="img" aria-label="Street map showing the depot location"></div>
  <svg class="abs" style="left:806px;top:100px" width="28" height="40" viewBox="0 0 28 40"><path d="M14 0C6 0 0 6 0 14c0 10 14 26 14 26s14-16 14-26C28 6 22 0 14 0z" fill="#d23a2a"/><circle cx="14" cy="14" r="5" fill="#fff"/></svg>
  <span class="btn">Send Now</span>
</div>

<footer class="abs footer"></footer>
<div class="abs f-brand"><div class="brand-mark"></div><div><div class="brand-name">HBR</div><div style="font-size:24px;font-weight:700;letter-spacing:4px">PLANT HIRE</div></div></div>
<div class="abs socials"><i></i><i></i><i></i><i></i><i></i></div>
<p class="abs copy" style="color:#fff">© Copyrights 2024 HBR Plant Hire | All Rights Reserved</p>
<div class="abs f-col f-links" style="color:#fff"><h5>QUICK LINKS</h5><ul><li>Home</li><li>About us</li><li>Machine Operator</li><li>Jobs</li><li>Plant Hire</li><li>Attachments Hire</li><li>Policies</li></ul></div>
<div class="abs f-col f-do" style="color:#fff"><h5>WHAT WE DO</h5><ul><li>Articulated Dump Trucks Hire</li><li>Dozer Hire</li><li>Excavator Diggers Hire</li><li>Grader Hire</li><li>Attachments Hire</li><li>Backhoe Hire</li><li>Compactors Hire</li><li>Loader Hire</li><li>Skid Steer Hire</li><li>Water Cart Hire</li></ul></div>
</body>
</html>
```